Web Developer Wordpress theme

I'm a web developer but a poor designer so i need somebody to design me a cool and professional WordPress theme. I specialize in shopping cart developments and modifications as well as hosting for these system so would like the design to show this off. I am UK based and want this to also come across in the design.
As for colors and layout i am open mined just use your imaginantion i will let know what i think of your designs.
also forgot to mention my business name is valtrique
and my exsiting site is valtrique.co.uk

```html
<!DOCTYPE html>
<html lang="en">
<head>
<meta charset="utf-8">
<title>Valtrique – Serious Web Development</title>
<link href="https://fonts.googleapis.com/css2?family=Roboto+Condensed:ital,wght@0,400;0,700;1,400&family=Arimo:wght@400;700&display=swap" rel="stylesheet">
<style>
:root{
  --white:#ffffff;
  --ink:#333333;
  --orange:#f28a00;
  --orange-deep:#e06f00;
  --navy:#0d5b9e;
  --navy-dark:#064a82;
  --cyan:#0aa6dc;
  --sky:#02a6ee;
}
*{margin:0;padding:0;box-sizing:border-box}
html,body{width:1200px;height:709px;overflow:hidden;background:var(--white)}
body{position:relative;font-family:"Arimo",Arial,sans-serif;color:var(--white)}
.site-header{position:absolute;left:0;top:0;width:1200px;height:130px;background:var(--white)}
.brand{position:absolute;left:115px;top:20px;display:flex;align-items:center;gap:10px}
.brand-mark{width:52px;height:52px;border-radius:50%;background:var(--cyan)}
.brand-name{font-family:"Roboto Condensed",sans-serif;font-weight:700;font-size:58px;line-height:1;color:var(--orange);letter-spacing:-1px}
.brand-tagline{position:absolute;left:198px;top:87px;font-size:11px;letter-spacing:2px;color:#555;font-weight:700}
.main-nav{position:absolute;top:48px;left:573px;display:flex;font-family:"Roboto Condensed",sans-serif;font-size:16px}
.main-nav a{color:var(--orange);text-decoration:none;height:30px;line-height:30px;margin-right:40px;white-space:nowrap}
.main-nav a.current{position:relative;background:linear-gradient(#f2f2f2,#dcdcdc);color:var(--ink);border-radius:15px;width:80px;text-align:center;margin-right:21px}
.main-nav a.current::after{content:"";position:absolute;left:20px;bottom:-12px;border-left:6px solid transparent;border-right:6px solid transparent;border-top:13px solid #dcdcdc;transform:skewX(20deg)}
.stage{position:absolute;left:0;top:124px;width:1200px;height:537px;background:radial-gradient(ellipse at 40% 40%,#1267ad,var(--navy) 70%)}
.edge{position:absolute;left:0;top:-7px;width:1200px;height:8px;display:block}
.about-tag{position:absolute;left:115px;top:57px;width:310px;height:47px;background:linear-gradient(90deg,var(--cyan) 40%,rgba(10,166,220,0));border-radius:8px 0 0 0;font-family:"Roboto Condensed",sans-serif;font-weight:700;font-size:32px;line-height:49px;padding-left:18px}
.about-tag::after{content:"";position:absolute;left:20px;top:47px;border-left:22px solid var(--cyan);border-bottom:12px solid transparent}
.about-text{position:absolute;left:155px;top:123px;width:600px;white-space:nowrap;font-family:"Roboto Condensed",sans-serif;font-style:italic;font-size:24px;line-height:36px}
.services{position:absolute;left:752px;top:14px;width:342px;height:310px}
.services text{font-family:"Roboto Condensed",sans-serif;font-size:25px;fill:var(--white);text-anchor:middle}
.panel{position:absolute;width:250px}
.panel-icon{position:absolute;left:-60px;top:0;width:52px;height:52px;border-radius:50%;background:var(--cyan)}
.panel-icon svg{width:52px;height:52px}
.panel h2{font-family:"Roboto Condensed",sans-serif;font-weight:700;font-size:30px;color:var(--orange);line-height:32px;margin-bottom:18px}
.panel p{font-size:12px;line-height:20px;width:225px}
.panel a{display:block;margin-top:15px;color:var(--cyan);font-size:13px}
.testimonials{left:185px;top:342px}
.latest{left:514px;top:349px}
.latest h2{margin-bottom:11px}
.contact{left:836px;top:349px}
.contact h2{margin-bottom:18px}
.contact .field{display:block;width:240px;height:27px;margin-bottom:11px;background:var(--navy-dark);color:var(--cyan);font-size:12px;line-height:27px;padding-left:9px}
.submit{display:flex;align-items:center;justify-content:space-between;width:92px;height:23px;margin-top:18px;border-radius:12px;background:linear-gradient(#f8a532,var(--orange-deep));font-size:11px;font-weight:700;padding:0 4px 0 18px}
.submit i{width:16px;height:16px;border-radius:50%;background:var(--white)}
.site-footer{position:absolute;left:0;top:661px;width:1200px;height:48px;background:var(--sky)}
.copyright{position:absolute;left:115px;top:18px;font-size:12px}
.social{position:absolute;top:9px;width:32px;height:32px;border-radius:50%;background:var(--white)}
</style>
</head>
<body>
<header class="site-header">
  <div class="brand"><span class="brand-mark"></span><span class="brand-name">valtrique</span></div>
  <div class="brand-tagline">serious web developement</div>
  <nav class="main-nav">
    <a class="current" href="#">Home</a><a href="#">About Us</a><a href="#">Services</a><a href="#">Addons</a><a href="#">Contact</a><a href="#">Blog</a>
  </nav>
</header>
<main class="stage">
  <svg class="edge" width="1200" height="8" viewBox="0 0 1200 8" preserveAspectRatio="none" aria-hidden="true">
    <defs>
      <pattern id="wave" width="12" height="8" patternUnits="userSpaceOnUse">
        <path d="M0 8 V4 Q3 0 6 4 Q9 8 12 4 V8 Z" fill="#0d5b9e"/>
      </pattern>
    </defs>
    <rect width="1200" height="8" fill="url(#wave)"/>
  </svg>
  <div class="about-tag">About Me</div>
  <p class="about-text">Valtrique, is a freelance web developer specializing in<br>online&nbsp; shopping cart solution&nbsp; whether it is just a simple<br>Paylume cart or a full blown shopping management system<br>we customize and style it to your requirements</p>
  <svg class="services" viewBox="0 0 342 310" aria-label="Service areas">
    <circle cx="159" cy="98" r="98" fill="#7dc82b" opacity=".95"/>
    <circle cx="99" cy="208" r="98" fill="#0ab8e6" opacity=".9"/>
    <circle cx="241" cy="208" r="98" fill="#c9821f" opacity=".85"/>
    <text x="159" y="71">Shopping Cart</text><text x="161" y="101">Software</text>
    <text x="81" y="228">Cartwell</text><text x="84" y="258">Templates</text>
    <text x="268" y="228">Cartwell</text><text x="271" y="258">Addons</text>
  </svg>
  <section class="panel testimonials">
    <span class="panel-icon"><svg viewBox="0 0 52 52"><path d="M16 36 L18 29 L32 15 L37 20 L23 34 Z" fill="#fff"/></svg></span>
    <h2>Testimonials</h2>
    <p>Lorem Ipsum has been the industry's standard dummy text ever since the 1500s, when an unknown printer took a galley of type and scrambled it to make</p>
    <a href="#">Lorem Ipsum</a>
  </section>
  <section class="panel latest">
    <span class="panel-icon" style="top:-7px"><svg viewBox="0 0 52 52"><path d="M17 13 H29 L35 19 V38 H17 Z" fill="none" stroke="#fff" stroke-width="3"/><path d="M31 30 H39 M35 26 V34" stroke="#fff" stroke-width="3"/></svg></span>
    <h2>Latest Post</h2>
    <p>Lorem Ipsum has been the industry's standard dummy text ever since the 1500s, when an unknown printer took a galley of type and scrambled it to make</p>
    <a href="#">Lorem Ipsum</a>
  </section>
  <section class="panel contact">
    <span class="panel-icon" style="left:-62px;top:-5px"><svg viewBox="0 0 52 52"><rect x="12" y="16" width="28" height="20" fill="none" stroke="#fff" stroke-width="2.5"/><path d="M12 16 L26 28 L40 16" fill="none" stroke="#fff" stroke-width="2.5"/></svg></span>
    <h2>Quick Contact</h2>
    <span class="field">Name</span>
    <span class="field">Email</span>
    <span class="submit">SUBMIT<i></i></span>
  </section>
</main>
<footer class="site-footer">
  <span class="copyright">Website content Copyrighted Valtrique 2012.</span>
  <span class="social" style="left:958px" aria-label="Social profile"></span>
  <span class="social" style="left:1005px" aria-label="Social profile"></span>
  <span class="social" style="left:1053px" aria-label="Social profile"></span>
</footer>
</body>
</html>
```